Business card design for sustainable building and development company

Need a business card design for a new sustainable building and real estate development company in the San Francisco Bay area. Name of company is "Tovrin Advisors, LLC" and we provide "Sustainable building, energy and development services" for residential and non residential projects. We'd like the following colors used but not all area required: green, gray, blue. Design should communicate innovation, professionalism and sustainability. Our current website is www.tovrin-advisors.example. Another possible design idea is to have the following listed on the back of the card:
Certified: VERN QS, Eco Marker Rater, DOLM Rater, Terravue Inspector, KSO TQ Building Analyst. Its not a must but could be text that could be used for back of card. Overall, we are open to a simple, clean design and or one with more text than usual for a card.

Industry/Entity Type

Real Estate

Contact Information for Business Card

Name on card: Mark J. Halvik
Title for Name: Principal + Founder
Phone: 555.814.0627
Email: mhalvik@tovrin-advisors.example
Website: www.tovrin-advisors.example

Also, please add the following for address:
Bellhaven, California

Requirements
Nice to have
• If you can integrate the outline of a skyline on the backside of the card and if it looks good, I would like to see the design
Should not have
• a barcode;

```html
<!DOCTYPE html>
<html lang="en">
<head>
<meta charset="utf-8">
<title>Tovrin Advisors — Business Card</title>
<link href="https://fonts.googleapis.com/css2?family=Montserrat:wght@500;700&family=Open+Sans:wght@400;600&display=swap" rel="stylesheet">
<style>
  :root {
    --brand-green: #5aae3c;
    --logo-green: #6dbb3a;
    --ink: #2e3133;
    --paper: #f7f7f5;
    --backdrop: #5d5f60;
    --title-tint: #d9efc9;
  }
  * { margin: 0; padding: 0; box-sizing: border-box; }
  html, body { width: 1200px; height: 1029px; overflow: hidden; }
  body { background: var(--backdrop); font-family: "Open Sans", sans-serif; color: var(--ink); }

  .card {
    position: absolute; left: 190px; width: 820px; height: 469px;
    background: var(--paper); overflow: hidden;
    box-shadow: 0 6px 18px rgba(0,0,0,.35);
  }
  .card--back { top: 34px; }
  .card--front { top: 526px; }
  .card__band { position: absolute; inset: 0; }
  .card__band path { fill: var(--brand-green); }

  .brand { position: absolute; display: flex; align-items: center; gap: 16px; }
  .brand__mark { width: 104px; height: 104px; border-radius: 50%; background: var(--logo-green); flex: none; }
  .brand__name { font-family: "Montserrat", sans-serif; font-weight: 700; font-size: 50px; color: var(--brand-green); line-height: 1; letter-spacing: .5px; }
  .brand__tagline { font-family: "Montserrat", sans-serif; font-weight: 500; font-size: 12.5px; text-transform: uppercase; color: var(--ink); margin-top: 6px; letter-spacing: .3px; }
  .card--back .brand { left: 160px; top: 70px; }
  .card--front .brand { left: 150px; top: 80px; }

  .site-line { position: absolute; left: 60px; top: 318px; font-size: 15px; text-transform: uppercase; color: var(--ink); letter-spacing: .4px; }

  .person { position: absolute; left: 60px; top: 300px; text-align: right; }
  .person__name { font-weight: 600; font-size: 26px; text-transform: uppercase; color: var(--ink); letter-spacing: .5px; }
  .person__title { font-size: 15px; text-transform: uppercase; color: var(--title-tint); letter-spacing: .5px; }

  .contact { position: absolute; left: 420px; top: 282px; list-style: none; font-size: 14.5px; text-transform: uppercase; letter-spacing: .3px; }
  .contact li { display: flex; align-items: center; gap: 16px; height: 25px; }
  .contact li.contact__address { margin-top: 22px; }
  .contact svg { width: 14px; height: 14px; fill: var(--ink); flex: none; }
</style>
</head>
<body>

<section class="card card--back">
  <svg class="card__band" viewBox="0 0 820 469" aria-hidden="true">
    <path d="M0,262 H350 Q368,262 370,280 L374,330 Q376,346 394,346 H820 V469 H0 Z"/>
  </svg>
  <div class="brand">
    <span class="brand__mark"></span>
    <div>
      <div class="brand__name">Tovrin Advisors</div>
      <div class="brand__tagline">Green building, energy &amp; project advisory services</div>
    </div>
  </div>
  <div class="site-line">www.tovrin-advisors.example</div>
</section>

<section class="card card--front">
  <svg class="card__band" viewBox="0 0 820 469" aria-hidden="true">
    <path d="M0,262 H350 Q368,262 370,280 L374,348 Q376,364 394,364 H820 V469 H0 Z"/>
  </svg>
  <div class="brand">
    <span class="brand__mark"></span>
    <div>
      <div class="brand__name">Tovrin Advisors</div>
      <div class="brand__tagline">Green building, energy &amp; project advisory services</div>
    </div>
  </div>

  <div class="person">
    <div class="person__name">Mark J. Halvik</div>
    <div class="person__title">Principal</div>
  </div>

  <ul class="contact">
    <li>
      <svg viewBox="0 0 24 24"><path d="M6.6 10.8a15 15 0 0 0 6.6 6.6l2.2-2.2c.3-.3.7-.4 1-.2 1.1.4 2.3.6 3.6.6.6 0 1 .4 1 1V20c0 .6-.4 1-1 1A17 17 0 0 1 3 4c0-.6.4-1 1-1h3.5c.6 0 1 .4 1 1 0 1.3.2 2.5.6 3.6.1.3 0 .7-.2 1z"/></svg>
      <span>555.814.0627</span>
    </li>
    <li>
      <svg viewBox="0 0 24 24"><path d="M2 5h20v14H2z M2 5l10 8 10-8"/></svg>
      <span>mhalvik@tovrin-advisors.example</span>
    </li>
    <li>
      <svg viewBox="0 0 24 24"><circle cx="12" cy="12" r="10"/></svg>
      <span>www.tovrin-advisors.example</span>
    </li>
    <li class="contact__address">
      <svg viewBox="0 0 24 24"><path d="M12 2a7 7 0 0 0-7 7c0 5 7 13 7 13s7-8 7-13a7 7 0 0 0-7-7zm0 9.5A2.5 2.5 0 1 1 12 6.5a2.5 2.5 0 0 1 0 5z"/></svg>
      <span>Bellhaven, California</span>
    </li>
  </ul>
</section>

</body>
</html>
```